Website Design for R W Builders: Showcasing Excellence in General Contracting

R W Builders, a leading general contractor based in California, is seeking a professional and engaging website design to effectively showcase our expertise, services, and commitment to excellence. The website will serve as a digital platform to represent our brand identity, highlight our portfolio, and attract potential clients in various sectors.

Key Objectives:

Reflect Company Identity: The website should accurately reflect the identity and values of R W Builders, including our dedication to quality, professionalism, and client satisfaction.
Showcase Services: Highlight our wide range of general contracting services, including but not limited to construction management, design-build, renovation, and commercial construction.
Portfolio Display: Display an extensive portfolio of past projects completed by R W Builders, showcasing our capabilities, craftsmanship, and successful outcomes.
Client Testimonials: Incorporate client testimonials and case studies to demonstrate our track record of delivering projects on time, within budget, and to the highest standards.
Contact Information: Ensure easy access to contact information, including phone number, email, and physical address, to facilitate communication with potential clients.
Responsive Design: Develop a responsive website design optimized for various devices and screen sizes, ensuring a seamless user experience across desktops, laptops, tablets, and smartphones.
Search Engine Optimization (SEO): Implement SEO best practices to enhance the visibility of the website on search engines, increasing organic traffic and generating leads.
User-Friendly Navigation: Create an intuitive and user-friendly navigation structure that enables visitors to easily find the information they need, such as services, portfolio, testimonials, and contact details.
Visual Appeal: Utilize visually appealing graphics, images, and layout designs to capture the attention of visitors and leave a lasting impression of professionalism and quality.
Compliance and Security: Ensure compliance with industry standards and regulations, as well as implementing necessary security measures to protect user data and privacy.

```html
<!DOCTYPE html>
<html lang="en">
<head>
<meta charset="utf-8">
<title>R W Builders — General Contracting</title>
<link rel="stylesheet" href="https://fonts.googleapis.com/css2?family=Archivo:wght@700;800;900&family=Lato:wght@400;700&display=swap">
<style>
:root{
  --orange:#f25a0f;
  --orange-dark:#d94c08;
  --ink:#111111;
  --dark:#16181b;
  --text:#555555;
  --muted:#888888;
  --line:#d9d9d9;
  --white:#ffffff;
}
*{box-sizing:border-box;margin:0;padding:0}
html,body{width:1200px;height:5133px;overflow:hidden}
body{position:relative;background:var(--white);font-family:'Lato',sans-serif;color:var(--text)}
.abs{position:absolute}
.heading{font-family:'Archivo',sans-serif;font-weight:800;color:var(--ink);letter-spacing:.5px}
.eyebrow{font-family:'Lato',sans-serif;font-weight:700;color:var(--orange);font-size:27px;letter-spacing:.5px;display:flex;align-items:center;gap:20px}
.eyebrow .rule{display:block;width:70px;height:2px;background:var(--orange)}
.center-x{left:0;width:1200px;text-align:center;justify-content:center}
.btn{position:absolute;display:flex;align-items:center;justify-content:center;border-radius:20px;font-family:'Lato',sans-serif;font-weight:700;font-size:16px;height:36px}
.btn-solid{background:var(--orange);color:var(--white)}
.btn-ghost{background:var(--white);color:var(--orange)}
.photo{position:absolute}
.callus{position:absolute;display:flex;align-items:center;gap:18px}
.callus .dot{width:40px;height:40px;border-radius:50%;background:var(--orange);display:flex;align-items:center;justify-content:center}
.callus small{display:block;font-size:10px;color:var(--ink);font-weight:700}
.callus strong{display:block;font-family:'Archivo',sans-serif;font-weight:700;font-size:23px;color:var(--ink)}

/* top bar */
.topbar{left:0;top:0;width:1200px;height:44px;background:var(--orange);color:var(--white);font-size:15px;font-weight:700}
.topbar .socials{left:112px;top:14px;display:flex;gap:8px}
.topbar .socials span{width:14px;height:14px;background:var(--white);border-radius:2px}
.topbar .phone{left:230px;top:12px;display:flex;gap:10px;align-items:center}
.topbar .mail{right:112px;top:12px;display:flex;gap:10px;align-items:center}

/* nav */
.nav{left:0;top:44px;width:1200px;height:88px;background:var(--white)}
.nav a{position:absolute;top:38px;font-size:13px;color:#222;text-decoration:none;font-weight:700}
.brand-badge{left:500px;top:-10px;width:200px;height:182px;border-radius:0 0 100px 100px;background:var(--white);display:flex;flex-direction:column;align-items:center;justify-content:center;z-index:3}
.brand-badge .name{font-family:'Archivo',sans-serif;font-weight:800;font-size:24px;color:var(--ink);line-height:1.05;text-align:center}
.brand-badge .town{font-family:'Archivo',sans-serif;font-weight:800;font-size:13px;color:var(--ink);margin-top:8px}

/* hero */
.hero{left:0;top:132px;width:1200px;height:630px;overflow:hidden}
.hero-box{left:214px;top:144px;width:776px;height:270px;background:rgba(20,20,20,.78);border-radius:10px;text-align:center;color:var(--white)}
.hero-box h1{font-family:'Archivo',sans-serif;font-weight:800;font-size:66px;margin-top:40px;letter-spacing:1px}
.hero-box p{font-size:21px;margin-top:10px}

/* about */
.about-text{left:112px;top:1000px;width:460px;font-size:13.5px;line-height:32px;color:#444}
.about-text p+p{margin-top:32px}

/* services */
.svc-card{position:absolute;top:1836px;height:294px}
.svc-label{position:absolute;top:2150px;width:240px;text-align:center;color:var(--white);font-size:17px;font-weight:700}
.arrow-btn{position:absolute;width:26px;height:26px;border-radius:50%;display:flex;align-items:center;justify-content:center}

/* reviews */
.review{position:absolute;top:3614px;width:316px}
.review .pic{height:306px}
.review .who{margin-top:34px;display:flex;align-items:center;gap:22px;padding-left:0;font-size:15px}
.review .who b{color:var(--orange);font-weight:700}
.review .who span{color:#666}
.review .quote{font-family:'Archivo',sans-serif;font-weight:900;color:var(--orange);font-size:30px;line-height:20px;height:20px}
.review p{margin-top:14px;text-align:center;font-size:12.5px;line-height:27px;color:#666;padding:0 10px}

/* contact */
.contact-panel{left:112px;top:4420px;width:980px;height:480px;background:rgba(255,255,255,.93);border-bottom:3px solid var(--orange);box-shadow:0 6px 14px rgba(0,0,0,.12)}
.field{position:absolute;width:240px;border-bottom:1px solid var(--line);padding-bottom:12px;font-size:12px;color:#555}
.info{position:absolute;left:736px;display:flex;align-items:center;gap:14px;font-size:17px;color:#444}

/* footer */
.footer-nav a{position:absolute;top:4980px;font-size:15px;color:#222;text-decoration:none}
.foot-social{position:absolute;top:5026px;width:36px;height:36px;border-radius:50%;background:var(--orange)}
</style>
</head>
<body>

<!-- Top bar -->
<div class="abs topbar">
  <div class="abs socials"><span></span><span></span><span></span></div>
  <div class="abs phone">
    <svg width="14" height="14" viewBox="0 0 24 24"><path fill="#fff" d="M6.6 10.8a15 15 0 0 0 6.6 6.6l2.2-2.2a1 1 0 0 1 1-.25 11.4 11.4 0 0 0 3.6.6 1 1 0 0 1 1 1V20a1 1 0 0 1-1 1A17 17 0 0 1 3 4a1 1 0 0 1 1-1h3.5a1 1 0 0 1 1 1c0 1.25.2 2.45.6 3.6a1 1 0 0 1-.25 1z"/></svg>
    (555) 214-3090
  </div>
  <div class="abs mail">
    <svg width="15" height="12" viewBox="0 0 24 18"><path fill="#fff" d="M0 0h24v18H0zM2 2v1l10 7 10-7V2z"/></svg>
    RW@RWBUILDERS.BIZ
  </div>
</div>

<!-- Navigation -->
<nav class="abs nav">
  <a style="left:110px">HOME</a>
  <a style="left:216px">ABOUT US</a>
  <a style="left:348px">SERVICES</a>
  <a style="left:758px">PROJECT</a>
  <a style="left:882px">REVIEWS</a>
  <a style="left:1005px">CONTACT US</a>
  <div class="abs brand-badge">
    <div class="name">R W<br>BUILDERS</div>
    <div class="town">RIDGEWELL, CA</div>
  </div>
</nav>

<!-- Hero -->
<section class="abs hero">
  <div class="abs" role="img" aria-label="Excavator demolishing a white house wall on a construction site" style="inset:0;background:linear-gradient(100deg,#c9c4bb 0%,#8a8578 35%,#6f7561 60%,#a88a3c 80%,#4d5544 100%)"></div>
  <svg class="abs" style="left:0;top:500px" width="1200" height="130" viewBox="0 0 1200 130" preserveAspectRatio="none">
    <polygon points="0,100 600,18 1200,100 1200,130 0,130" fill="#f25a0f"/>
    <polygon points="0,130 600,28 1200,130" fill="#ffffff"/>
  </svg>
  <div class="abs hero-box">
    <h1>R W BUILDERS</h1>
    <p>An 8(a) Small Business Prime Contractor</p>
  </div>
  <div class="btn btn-solid" style="left:456px;top:324px;width:140px">Get Started</div>
  <div class="btn btn-ghost" style="left:608px;top:324px;width:136px">Contact Us</div>
</section>

<!-- About -->
<section>
  <div class="abs eyebrow" style="left:112px;top:868px">ABOUT US <span class="rule"></span></div>
  <h2 class="abs heading" style="left:112px;top:918px;font-size:48px">WHO WE ARE</h2>
  <div class="abs about-text">
    <p>Ray Whitman, the sole owner and CEO/President of R W Builders (RWB) originally started the company in 2013. Since, RWB has been a thriving 8(a) certified General Contractor, consistently deliv The company has developed experience with civil, concrete, paving, grading and other small purchase order type projects.</p>
    <p>With vast experience in the trades, site superintendence, safety, quality control, and all aspects of general contracting, R W Builders can plan, manage and execute building construction projects in all sizes under any delivery method: design-build, CM at Risk, or design-bid-build.</p>
  </div>
  <div class="btn btn-solid" style="left:112px;top:1372px;width:136px">Read More</div>
  <div class="callus" style="left:266px;top:1370px">
    <div class="dot"><svg width="18" height="18" viewBox="0 0 24 24"><path fill="#fff" d="M6.6 10.8a15 15 0 0 0 6.6 6.6l2.2-2.2a1 1 0 0 1 1-.25 11.4 11.4 0 0 0 3.6.6 1 1 0 0 1 1 1V20a1 1 0 0 1-1 1A17 17 0 0 1 3 4a1 1 0 0 1 1-1h3.5a1 1 0 0 1 1 1c0 1.25.2 2.45.6 3.6a1 1 0 0 1-.25 1z"/></svg></div>
    <div><small>CALL US:</small><strong>(555) 214-3090</strong></div>
  </div>
  <div class="photo" role="img" aria-label="Two engineers in hard hats reviewing a tablet in a warehouse" style="left:610px;top:868px;width:480px;height:554px;border-radius:14px;background:linear-gradient(160deg,#8a6a48 0%,#c9a77c 35%,#e0b72e 55%,#5f5550 100%)"></div>
</section>

<!-- Services -->
<section>
  <svg class="abs" style="left:0;top:1572px" width="1200" height="850" viewBox="0 0 1200 850" preserveAspectRatio="none">
    <defs>
      <linearGradient id="svcBg" x1="0" y1="0" x2="0" y2="1">
        <stop offset="0" stop-color="#0d0f12"/><stop offset=".6" stop-color="#1a1c1f"/><stop offset="1" stop-color="#2b2724"/>
      </linearGradient>
    </defs>
    <polygon points="0,88 600,8 1200,88 1200,0 0,0" fill="#fff"/>
    <polygon points="0,88 600,8 1200,88 1200,96 600,18 0,96" fill="#f25a0f"/>
    <polygon points="0,96 600,18 1200,96 1200,844 600,768 0,844" fill="url(#svcBg)"/>
  </svg>
  <div class="abs eyebrow center-x" style="top:1676px;display:flex"><span class="rule"></span>SERVICES<span class="rule"></span></div>
  <h2 class="abs heading center-x" style="top:1730px;font-size:48px;color:#fff">WHAT WE OFFER</h2>

  <div class="svc-card" role="img" aria-label="Modern glass elevator shaft" style="left:88px;width:262px;clip-path:polygon(8% 0,100% 0,92% 100%,0 100%);background:linear-gradient(180deg,#9aa3ad,#4d545c 60%,#272b30)"></div>
  <div class="svc-card" role="img" aria-label="Excavator breaking concrete during demolition" style="left:344px;width:262px;clip-path:polygon(8% 0,100% 0,92% 100%,0 100%);background:linear-gradient(180deg,#7f93a6,#b89a45 45%,#8c8378)"></div>
  <div class="svc-card" role="img" aria-label="Worker installing white kitchen cabinets" style="left:600px;width:262px;clip-path:polygon(8% 0,100% 0,92% 100%,0 100%);background:linear-gradient(180deg,#e9e6df,#cfc8bb 60%,#a99d88)"></div>
  <div class="svc-card" role="img" aria-label="Landscaped garden with stone paving" style="left:856px;width:254px;clip-path:polygon(8% 0,100% 0,100% 100%,0 100%);background:linear-gradient(180deg,#4c6a34,#8c6a4a 45%,#77746e)"></div>

  <div class="svc-label" style="left:98px">ELEVATOR</div>
  <div class="svc-label" style="left:354px">DEMOLITION</div>
  <div class="svc-label" style="left:608px">REMODELS</div>
  <div class="svc-label" style="left:862px">LANDSCAPING</div>

  <div class="arrow-btn" style="left:45px;top:1971px;background:#555"><svg width="10" height="10" viewBox="0 0 10 10"><path d="M7 1 3 5l4 4" stroke="#ccc" stroke-width="2" fill="none"/></svg></div>
  <div class="arrow-btn" style="left:1129px;top:1971px;background:#fff"><svg width="10" height="10" viewBox="0 0 10 10"><path d="M3 1l4 4-4 4" stroke="#111" stroke-width="2" fill="none"/></svg></div>

  <div class="btn btn-solid" style="left:386px;top:2220px;width:204px">Specialized Services</div>
  <div class="btn btn-ghost" style="left:610px;top:2220px;width:204px">General Contracting</div>
</section>

<!-- Portfolio -->
<section>
  <div class="abs eyebrow center-x" style="top:2460px;display:flex"><span class="rule"></span>OUR WORKS<span class="rule"></span></div>
  <h2 class="abs heading center-x" style="top:2512px;font-size:48px">PROJECT PORTFOLIO</h2>
  <div class="photo" role="img" aria-label="Electrician installing pendant lights in a bright room" style="left:112px;top:2620px;width:484px;height:310px;background:linear-gradient(135deg,#eeeeec,#d9d7d2 55%,#b7b2a8)"></div>
  <div class="photo" role="img" aria-label="Curved stone garden border with green shrubs" style="left:602px;top:2620px;width:490px;height:310px;background:linear-gradient(135deg,#5d7c2e,#8fa34c 50%,#3e5424)"></div>
  <div class="photo" role="img" aria-label="Modern glass shower enclosure with grey tiles" style="left:112px;top:2936px;width:322px;height:320px;background:linear-gradient(135deg,#f1f1f1,#c9cbcd 60%,#9fa3a6)"></div>
  <div class="photo" role="img" aria-label="Yellow demolition machine crushing rubble" style="left:440px;top:2936px;width:324px;height:320px;background:linear-gradient(135deg,#7d7b77,#a9a59e 45%,#d6a12a)"></div>
  <div class="photo" role="img" aria-label="Stone house with wooden garage doors and paved driveway" style="left:770px;top:2936px;width:322px;height:320px;background:linear-gradient(180deg,#b8a995,#7a4a2c 50%,#a39584)"></div>
  <div class="btn btn-solid" style="left:412px;top:3312px;width:136px">View More</div>
  <div class="callus" style="left:566px;top:3306px">
    <div class="dot"><svg width="18" height="18" viewBox="0 0 24 24"><path fill="#fff" d="M6.6 10.8a15 15 0 0 0 6.6 6.6l2.2-2.2a1 1 0 0 1 1-.25 11.4 11.4 0 0 0 3.6.6 1 1 0 0 1 1 1V20a1 1 0 0 1-1 1A17 17 0 0 1 3 4a1 1 0 0 1 1-1h3.5a1 1 0 0 1 1 1c0 1.25.2 2.45.6 3.6a1 1 0 0 1-.25 1z"/></svg></div>
    <div><small>CALL US:</small><strong>(555) 214-3090</strong></div>
  </div>
</section>

<!-- Reviews -->
<section>
  <div class="abs eyebrow" style="left:112px;top:3470px">REVIEWS <span class="rule"></span></div>
  <h2 class="abs heading" style="left:112px;top:3516px;font-size:48px">HAPPY CUSTOMERS</h2>
  <div class="btn btn-solid" style="left:954px;top:3506px;width:138px">View More</div>

  <div class="arrow-btn" style="left:45px;top:3742px;background:#ccc"><svg width="10" height="10" viewBox="0 0 10 10"><path d="M7 1 3 5l4 4" stroke="#fff" stroke-width="2" fill="none"/></svg></div>
  <div class="arrow-btn" style="left:1129px;top:3742px;background:#111"><svg width="10" height="10" viewBox="0 0 10 10"><path d="M3 1l4 4-4 4" stroke="#fff" stroke-width="2" fill="none"/></svg></div>

  <div class="review" style="left:112px">
    <div class="pic" role="img" aria-label="Utility equipment on a rural site under a cloudy sky" style="background:linear-gradient(180deg,#5d7590,#8d9aa4 50%,#5b5a44)"></div>
    <div class="who"><span class="quote">&ldquo;</span><div><b>Daniel Brooks</b><span>, Lorem</span></div></div>
    <p>On the other hand, we denounce with righteous indignation and dislike men who are so beguiled and demoralized by the charms</p>
  </div>
  <div class="review" style="left:444px">
    <div class="pic" role="img" aria-label="Truck driving on a highway at sunset" style="background:linear-gradient(180deg,#3f4a5a,#e59a3c 45%,#2e3138)"></div>
    <div class="who"><span class="quote">&ldquo;</span><div><b>Daniel Brooks</b><span>, Lorem</span></div></div>
    <p>On the other hand, we denounce with righteous indignation and dislike men who are so beguiled and demoralized by the charms</p>
  </div>
  <div class="review" style="left:776px">
    <div class="pic" role="img" aria-label="Surveyor with plans on a grassy building site" style="background:linear-gradient(180deg,#b8c2cc,#d9dce0 40%,#6d8f3d)"></div>
    <div class="who"><span class="quote">&ldquo;</span><div><b>Daniel Brooks</b><span>, Lorem</span></div></div>
    <p>On the other hand, we denounce with righteous indignation and dislike men who are so beguiled and demoralized by the charms</p>
  </div>
</section>

<!-- Contact -->
<section>
  <div class="abs" role="img" aria-label="Construction crew in safety vests on a site with machinery and autumn trees" style="left:0;top:4200px;width:1200px;height:600px;background:linear-gradient(180deg,#a8763a,#c99b5f 35%,#bfb3a3 70%,#d4cbbd)"></div>
  <div class="abs contact-panel"></div>
  <div class="abs eyebrow center-x" style="top:4490px;display:flex"><span class="rule"></span>CONTACT US<span class="rule"></span></div>
  <h2 class="abs heading center-x" style="top:4538px;font-size:48px">GET IN TOUCH WITH US</h2>

  <div class="field" style="left:176px;top:4650px">First Name</div>
  <div class="field" style="left:444px;top:4650px">Last Name</div>
  <div class="field" style="left:176px;top:4714px">Email Address</div>
  <div class="field" style="left:444px;top:4714px">Contact Number</div>
  <div class="field" style="left:176px;top:4794px">Message</div>
  <div class="btn btn-solid" style="left:446px;top:4790px;width:236px;height:42px;border-radius:22px">Submit Here</div>

  <div class="info" style="top:4664px"><svg width="14" height="18" viewBox="0 0 14 20"><path fill="#f25a0f" d="M7 0a7 7 0 0 0-7 7c0 5 7 13 7 13s7-8 7-13a7 7 0 0 0-7-7zm0 9.5A2.5 2.5 0 1 1 7 4.5a2.5 2.5 0 0 1 0 5z"/></svg>P.O. Box 4821 Ridgewell, CA 93999</div>
  <div class="info" style="top:4712px"><svg width="16" height="16" viewBox="0 0 24 24"><path fill="#f25a0f" d="M6.6 10.8a15 15 0 0 0 6.6 6.6l2.2-2.2a1 1 0 0 1 1-.25 11.4 11.4 0 0 0 3.6.6 1 1 0 0 1 1 1V20a1 1 0 0 1-1 1A17 17 0 0 1 3 4a1 1 0 0 1 1-1h3.5a1 1 0 0 1 1 1c0 1.25.2 2.45.6 3.6a1 1 0 0 1-.25 1z"/></svg>(555) 214-3090</div>
  <div class="info" style="top:4758px"><svg width="16" height="12" viewBox="0 0 24 18"><path fill="#f25a0f" d="M0 0h24v18H0zM2 2v1l10 7 10-7V2z"/></svg>rw@rwbuilders.biz</div>
  <div class="info" style="top:4804px"><svg width="16" height="16" viewBox="0 0 20 20"><circle cx="10" cy="10" r="9" fill="none" stroke="#f25a0f" stroke-width="2"/><path d="M1 10h18M10 1c3 3 3 15 0 18M10 1c-3 3-3 15 0 18" fill="none" stroke="#f25a0f" stroke-width="1.6"/></svg>www.rwbuilders.biz</div>
</section>

<!-- Footer -->
<footer>
  <div class="abs" style="left:112px;top:4968px;width:130px;text-align:center">
    <div class="heading" style="font-size:24px;line-height:1.05">R W<br>BUILDERS</div>
    <div class="heading" style="font-size:12px;margin-top:8px">RIDGEWELL, CA</div>
  </div>
  <div class="footer-nav">
    <a style="left:360px">Home</a>
    <a style="left:478px">About Us</a>
    <a style="left:618px">Services</a>
    <a style="left:752px">Project</a>
    <a style="left:878px">Reviews</a>
    <a style="left:1012px">Contact Us</a>
  </div>
  <span class="foot-social" style="left:922px"></span>
  <span class="foot-social" style="left:966px"></span>
  <span class="foot-social" style="left:1010px"></span>
  <span class="foot-social" style="left:1054px"></span>
  <div class="abs" style="right:108px;top:5088px;font-size:12px;color:#555">(C) Copyright 2024 | All Rights Reserved</div>
  <div class="abs" style="left:0;top:5126px;width:1200px;height:7px;background:var(--orange)"></div>
</footer>

</body>
</html>
```